Water filter company needs packaging designs

Tonivo is a new company that makes eco-friendly water filter for consumers . we currently need designs for our 13 stage water filter, alkaline filter and their respective replacement cartridges.we would like to see a final design that reflect Eco-friendliness, safeness, uniqueness, healthiness,cleanliness and life.

https://www.filemarrowa.com/s/k8r2mw7qtz4xnpa/image%201.png
https://www.filemarrowa.com/s/h3d71vqx94jcm2e/image%204%20%281%29.png
https://www.filemarrowa.com/s/w6tnb8ekz2rfyuo/image%206%20png.png"

some of the images i attached for use are also available a this dropbox link

https://www.filemarrowa.com/sh/pqvlo4tgyaekmsd/KWraTfX_M3?n=58207341
Updates

sorry everyone i forgot to add the dimensions.
13 stage and alkaline filter have the same dimensions of

Size { W x H x L }: 4.5 x 12 x 5.375 INCHES
their cartidges have the same dimensions of
Size { W x H x L }: 3.125 x 10 x 3.125 INCHES

include "Made in U.S.A" on all packaging boxes.

I just found out that the people at quilmstack screwed up the order of the files I sent in for upload.Here is an update on that . For 13 stage water filter and it's replacement cartridge box, use the files with following names only  and any corresponding description - 13 stage cartridge, image 1, image 4,image 2, image 6 ,logo,front panel image,13 stage water filter and 13 stage water filter replacement cartridge.For alkaline filter and it;s replacement filter, use files with the following names only and any corresponding description-  8 stage cartridge,active girl,front panel image,glass girl, jumping girl,yoga girl,tonivo alkaline water filter, tonivo alkaline water filter replacement cartridge,logo

uploaded water splash image for background.You can revise your work with that if you wish to.Thanks

Target Market(s)

consumers for home use

Industry/Entity Type

It Company

Requirements
Must have
• must use all photos attached with appropriate descriptions
must be in retail packaging

```html
<!DOCTYPE html>
<html lang="en">
<head>
<meta charset="utf-8">
<title>Mineralized Tonivo Alkaline Water Filter – Box Panels</title>
<link href="https://fonts.googleapis.com/css2?family=Jost:ital,wght@0,400;0,500;0,600;0,700;1,400&display=swap" rel="stylesheet">
<style>
  :root {
    --bg-top: #f2f2f2;
    --bg-bottom: #d9d9d9;
    --teal-light: #1f9ba6;
    --teal-mid: #17808f;
    --teal-deep: #0f5f73;
    --navy: #1b2f7a;
    --navy-deep: #162566;
    --ink: #ffffff;
    --ink-soft: #dfeff3;
  }
  * { box-sizing: border-box; margin: 0; padding: 0; }
  html, body { width: 1200px; height: 845px; overflow: hidden; }
  body {
    background: linear-gradient(180deg, var(--bg-top), var(--bg-bottom));
    font-family: "Jost", sans-serif;
    color: var(--ink);
  }
  .carton {
    position: absolute;
    left: 250px; top: 30px;
    width: 700px; height: 785px;
    display: flex;
    box-shadow: 0 18px 40px rgba(0,0,0,.25);
  }
  .panel {
    width: 350px; height: 100%;
    padding: 22px 20px;
    font-size: 11px; line-height: 1.32;
  }
  .panel--side {
    background: linear-gradient(180deg, var(--teal-light) 0%, var(--teal-mid) 35%, var(--teal-deep) 100%);
  }
  .panel--back {
    background: linear-gradient(180deg, var(--teal-light) 0%, var(--teal-mid) 50%, var(--teal-deep) 100%);
    text-align: center;
    border-left: 1px solid rgba(255,255,255,.08);
  }
  .intro { text-align: center; font-size: 11.5px; }
  .contaminants { margin-top: 12px; font-style: italic; font-size: 9px; text-align: center; color: var(--ink-soft); }
  .stages {
    margin: 14px -6px 0;
    background: linear-gradient(180deg, var(--navy) 0%, var(--navy-deep) 100%);
    border-radius: 14px;
    padding: 14px 14px 16px;
    text-align: center;
  }
  .stage + .stage { margin-top: 11px; }
  .stage__title { font-weight: 600; font-size: 11.5px; letter-spacing: .3px; }
  .stage__text { font-size: 11px; }
  .product-title { font-weight: 700; font-size: 12.5px; }
  .product-tag { font-size: 12px; margin-top: 2px; }
  .back-copy p { margin-top: 11px; font-size: 10.5px; }
  .closing { margin-top: 20px; font-size: 11.5px; }
  .eco-seal { display: block; margin: 22px auto 0; }
  .warranty { margin-top: 22px; font-weight: 600; font-size: 11px; }
  .warranty strong { display: block; font-size: 12px; letter-spacing: .4px; }
  .usage { margin-top: 14px; font-size: 11.5px; }
  .fineprint { margin-top: 14px; font-size: 8px; font-style: italic; text-align: left; color: var(--ink-soft); }
  .warning { font-weight: 600; }
</style>
</head>
<body>
<main class="carton">
  <section class="panel panel--side">
    <p class="intro">The truly unique and advanced Mineralized Tonivo Alkaline Water Filter removes dozens of harmful particles and other contaminants* below the U.S. EPA recommended content levels. The Mineralized Tonivo Alkaline Water Filter provides 13 unique filtration stages that prevent these particles from proceeding into your water. At the same time, this advanced filtration system remineralizes your clean water with calcium, potassium and other vital minerals that your body needs!</p>
    <p class="contaminants">*Contaminants include: Chlorine, cysts, heavy metals, herbicides, VOCs, asbestos, Giardia, arsenic, bromide, PBCs, bacteria, protozoa, radiation particles, medication residue, hydrogen sulfide, pesticides, trihalomethanes, cadmium, petrochemicals, sediment and many others.</p>
    <div class="stages">
      <div class="stage"><h3 class="stage__title">STAGE 1</h3><p class="stage__text">A layer of granular active carbon (G.A.C), which reduces carcinogenic particles and other harmful organic contaminants.</p></div>
      <div class="stage"><h3 class="stage__title">STAGE 2</h3><p class="stage__text">A primary 5-micron filter pad filters tiny particles from water, such as minute solids and sediment.</p></div>
      <div class="stage"><h3 class="stage__title">STAGE 3</h3><p class="stage__text">Alkaline beads, which increase pH level leaving essential minerals like magnesium, potassium, calcium etc in your water.</p></div>
      <div class="stage"><h3 class="stage__title">STAGE 4</h3><p class="stage__text">A second 5-micron filter pad, removes additional small particles and sediment.</p></div>
      <div class="stage"><h3 class="stage__title">STAGE 5</h3><p class="stage__text">Zeolite layer, which is a natural porous rock, eliminates strong odors and poor taste in water.</p></div>
      <div class="stage"><h3 class="stage__title">STAGE 6</h3><p class="stage__text">A third 5-micron filter pad, removes additional small particles and sediment.</p></div>
      <div class="stage"><h3 class="stage__title">STAGE 7</h3><p class="stage__text">Calcite, which increases water pH and reduces its acidic thereby, renders a favorable recommended level of alkalinity.</p></div>
      <div class="stage"><h3 class="stage__title">STAGE 8</h3><p class="stage__text">0.5 micron carbon block eliminates organic contaminants, like pesticides, herbicides, arsenic, lead, mercury and carcinogens such as trihalomethane.</p></div>
    </div>
  </section>

  <section class="panel panel--back">
    <h2 class="product-title">Mineralized Tonivo Alkaline Water Filter</h2>
    <p class="product-tag">For the purest water that hydrates and provides vital minerals!</p>
    <div class="back-copy">
      <p>Developed by a leading microbiologist. Patent pending Mineralized Tonivo Alkaline Water Filter offers 8 distinct filtration stages that reduce and eliminate some of the most harmful particles, while adding vital minerals to your delicious pure water!</p>
      <p>The Mineralized Tonivo Alkaline Water Filter is also eco-friendly, created from natural filter materials. It's free of all BPA particles and is also biodegradable!</p>
      <p>The Mineralized Tonivo Alkaline Water Filter has been independently tested by a leading laboratory to insure the highest quality of construction and effective function.</p>
      <p>The Mineralized Tonivo Alkaline Water Filter creates a remarkable pH level of only 8.3, which is ideal for most users.</p>
      <p>This heavy-duty filter provides over 1500 gallons of pure, delicious, alkaline water!</p>
    </div>
    <p class="closing">For the very best water, enjoy the advanced Mineralized Tonivo Alkaline Water Filter today!</p>
    <svg class="eco-seal" width="86" height="86" viewBox="0 0 86 86" role="img" aria-label="Eco-friendly seal">
      <circle cx="43" cy="43" r="40" fill="none" stroke="#ffffff" stroke-width="3"/>
      <circle cx="43" cy="43" r="30" fill="#ffffff" opacity=".9"/>
    </svg>
    <p class="warranty">We offer all of our valued customers with a complete <strong>ONE-YEAR WARRANTY</strong></p>
    <p class="usage">Mineralized Tonivo Alkaline Water Filters may be used with a standard water tap quickly and easily.</p>
    <p class="fineprint">Note: Depending upon usage, the Mineralized Tonivo Alkaline Water Filter will operate and create alkaline water for one year or approximately 1,500 gallons for a family of four.</p>
    <p class="fineprint warning">Warning: Use the Mineralized Tonivo Alkaline Water Filter with municipal water sources only.</p>
  </section>
</main>
</body>
</html>
```